Podiatry clinic requires a modern revamp and editing of existing website.

I would like a fresh new look and updated information for my current business website. An easy to navigate site with prominent address and phone number for call to action. We are a podiatry clinic that focuses on general and sports podiatry.
I would like 4 pages; including Home page, About Us, Services & Contact.
www.brambleridgepodiatry.net

Target Market(s)

Active working professionals.

Industry/Entity Type

Medical

Coding

Coded - Design and coding required

Number of Pages Required

4 page

Font styles to use
Sans Serif

Colors
6b449b

Requirements
Must have
• A modern look with logo and active images; clean and uncluttered. Visible phone number and address for call to action.
• 4 pages - Home, About Us, Services, Contact.
• Home page - update address & service logos.
• About Us - update of personal information.
• Services - Revamp of existing page.
• Contact page to include Google map, email & phone number.
Nice to have
• Ability to add content easily; eg. a blog or adding video onto Home page.
• Link to Facebook page.

```html
<!DOCTYPE html>
<html lang="en">
<head>
<meta charset="utf-8">
<title>Bramble Ridge Podiatry</title>
<link rel="stylesheet" href="https://fonts.googleapis.com/css2?family=Raleway:wght@400;500;600;700&family=Arimo:wght@400;700&display=swap">
<style>
:root{
  --brand:#6b449b;
  --header:#9a86c6;
  --deep:#3b2a66;
  --ink:#2a2a2a;
  --body:#4a4a4a;
  --accent:#f26b1d;
  --lilac:#a58fd2;
  --foot:#f4f4f6;
  --bottom:#272040;
  --line:#d8d8d8;
}
*{box-sizing:border-box;margin:0;padding:0}
html,body{width:1200px;height:2228px;overflow:hidden}
body{position:relative;font-family:"Arimo",Arial,sans-serif;color:var(--body);background:#fff}
.abs{position:absolute}

/* header */
.site-header{left:0;top:0;width:1200px;height:84px;background:var(--header);border-top:4px solid var(--brand)}
.brand{left:141px;top:14px;display:flex;align-items:center;gap:8px;font-family:"Raleway",sans-serif;font-weight:700;font-size:17px;color:#fff;line-height:1.05;width:150px}
.brand-mark{width:14px;height:40px;background:var(--brand);flex:none}
.main-nav{left:486px;top:54px;display:flex;gap:30px;font-family:"Raleway",sans-serif;font-weight:600;font-size:17px;color:#fff}
.main-nav .active{color:var(--accent);position:relative}
.main-nav .active::before{content:"";position:absolute;left:14px;top:-54px;border:9px solid transparent;border-top-color:var(--accent);border-bottom:0}
.nav-divider{left:879px;top:20px;width:1px;height:58px;background:rgba(255,255,255,.6)}
.call{left:905px;top:32px;display:flex;gap:12px;color:#fff}
.call-text small{display:block;font-size:14px}
.call-text strong{display:block;font-size:21px;font-weight:400;margin-top:2px}

/* hero */
.hero{left:0;top:84px;width:1200px;height:365px;display:flex}
.hero > div{height:100%}
.slide-arrow{top:300px;width:30px;height:34px;border:1px solid rgba(255,255,255,.7);background:rgba(0,0,0,.25)}
.tagline{left:0;top:449px;width:1200px;height:52px;background:var(--brand);color:#fff;text-align:center;font-family:"Raleway",sans-serif;font-weight:600;font-size:25px;line-height:52px}
.tagline b{font-weight:700}

/* welcome */
.section-title{font-family:"Raleway",sans-serif;font-weight:500;color:var(--ink)}
.welcome-title{left:126px;top:536px;font-size:30px}
.title-rule{left:126px;top:580px;width:546px;height:14px}
.welcome-copy{left:126px;top:604px;width:550px;font-size:13.5px;line-height:22px;color:#444}
.welcome-copy p{margin-bottom:12px}
.read-more{color:var(--ink);text-decoration:underline;font-size:14px}
.video{left:737px;top:554px;width:330px;height:222px;border-radius:4px;overflow:hidden;border:1px solid #222}

/* services */
.services{left:0;top:822px;width:1200px;height:531px;background:var(--deep)}
.notch{left:580px;width:0;height:0;border:20px solid transparent}
.services-title{left:0;top:856px;width:1200px;text-align:center;font-family:"Raleway",sans-serif;font-weight:500;font-size:31px;color:#fff}
.services-title span{color:var(--accent)}
.services-intro{left:0;top:932px;width:1200px;text-align:center;font-size:17px;color:#fff}
.service{width:300px;text-align:center;color:#fff}
.service-icon{width:128px;height:128px;border-radius:50%;background:#fff;border:5px solid #8f7cc0;margin:0 auto;display:flex;align-items:center;justify-content:center}
.service-art{width:96px;height:96px;border-radius:50%;background:radial-gradient(circle,#e4def0 0,#cfc6e3 100%)}
.service h3{font-family:"Raleway",sans-serif;font-weight:700;font-size:20px;margin-top:36px}
.service p{width:270px;margin:10px auto 0;font-size:15px;line-height:26px}
.service a{display:inline-block;margin-top:18px;color:var(--accent);text-decoration:underline;font-size:14px}
.service-divider{top:996px;width:1px;height:280px;background:rgba(255,255,255,.18)}

/* news + accreditations */
.news-band{left:0;top:1353px;width:1200px;height:494px;background:radial-gradient(circle at 78% 18%,#efe4f0 0,#e0dde6 30%,#d6d6dc 60%,#cfd0d6 100%)}
.block-title{font-family:"Raleway",sans-serif;font-weight:500;font-size:30px;color:var(--ink)}
.block-rule{height:2px;background:linear-gradient(90deg,var(--accent) 0 130px,#bbb 130px)}
.post{left:131px;width:440px;display:flex;gap:20px}
.post-thumb{width:108px;height:90px;border:2px solid #fff;flex:none;box-shadow:0 1px 3px rgba(0,0,0,.3)}
.post h4{font-size:12px;font-weight:700;color:#222;white-space:nowrap}
.post time{display:block;font-size:13px;color:var(--lilac);margin:4px 0 3px}
.post p{font-size:13px;line-height:19px;color:#444;width:295px}
.post p span{color:var(--lilac)}
.badge{width:205px;height:80px;background:#fff;border:1px solid #999;display:flex;align-items:center;justify-content:center}
.badge i{display:block;width:150px;height:44px;border-radius:6px}

/* call to action */
.cta{left:0;top:1847px;width:1200px;height:85px;background:var(--deep)}
.cta-button{left:195px;top:1870px;width:210px;height:40px;background:var(--lilac);color:#fff;font-family:"Raleway",sans-serif;font-weight:500;font-size:19px;line-height:40px;text-align:center}
.cta-text{left:429px;top:1865px;color:#fff;font-family:"Raleway",sans-serif;font-weight:500;font-size:20px;line-height:25px}
.cta-text em{font-style:normal;color:#ff5a2a}

/* footer */
.site-footer{left:0;top:1932px;width:1200px;height:251px;background:var(--foot)}
.foot-head{font-family:"Raleway",sans-serif;font-weight:600;font-size:18px;color:#333;padding-bottom:8px;border-bottom:1px dotted #bbb}
.quick-links{left:134px;top:1955px;width:132px}
.quick-links ul{list-style:none;margin-top:10px}
.quick-links li{font-size:13.5px;color:#333;line-height:24.5px;padding-left:14px;position:relative}
.quick-links li::before{content:"›";position:absolute;left:0;color:#999}
.contact-col{left:352px;top:1955px;width:250px}
.contact-row{display:flex;gap:12px;font-size:14px;color:#333;line-height:18px;padding:14px 0;border-bottom:1px solid #ddd}
.hours-col{left:680px;top:1955px;width:170px}
.hours-col dl{font-size:13.5px;color:#333;line-height:18px}
.hours-col dd{margin-bottom:17px;padding-bottom:6px;border-bottom:1px solid #ddd}
.foot-logo{left:930px;top:1987px;width:166px;height:147px;background:var(--lilac);display:flex;align-items:center;justify-content:center;gap:10px;color:#fff;font-family:"Raleway",sans-serif;font-weight:700;font-size:20px;line-height:1.1}
.foot-logo i{width:16px;height:70px;background:var(--brand)}
.bottom-bar{left:0;top:2183px;width:1200px;height:45px;background:var(--bottom)}
.copyright{left:131px;top:2197px;font-size:14px;color:#ddd}
.social{top:2185px;width:32px;height:32px;border-radius:50%;background:#7a7a82}
</style>
</head>
<body>

<header class="abs site-header">
  <div class="abs brand"><span class="brand-mark"></span><span>Bramble Ridge Podiatry</span></div>
  <nav class="abs main-nav">
    <span class="active">Home</span><span>About Us</span><span>Services</span><span>Contact Us</span>
  </nav>
  <div class="abs nav-divider"></div>
  <div class="abs call">
    <svg width="28" height="28" viewBox="0 0 28 28" aria-hidden="true"><circle cx="14" cy="14" r="12.5" fill="none" stroke="#fff" stroke-width="1.5"/><path d="M10 8l3 3-1.5 2c1 2 2.5 3.5 4.5 4.5l2-1.5 3 3-2 2c-5 0-11-6-11-11z" fill="#fff"/></svg>
    <div class="call-text"><small>Call Us Today</small><strong>1300 555 014</strong></div>
  </div>
</header>

<section class="abs hero" role="img" aria-label="Row of action photos of athletes: golfer, runner, cyclist, dancer, footballer, basketball player">
  <div style="width:139px;background:linear-gradient(180deg,#6f8f76,#4e6a4f)"></div>
  <div style="width:241px;background:linear-gradient(180deg,#7e9267,#5b6d4a)"></div>
  <div style="width:224px;background:linear-gradient(180deg,#7b8f9e,#4e5a4c)"></div>
  <div style="width:276px;background:linear-gradient(180deg,#3a3a3c,#8a8a8c)"></div>
  <div style="width:202px;background:linear-gradient(180deg,#7d93b0,#a5532f)"></div>
  <div style="width:118px;background:linear-gradient(180deg,#4f3c3a,#6b5143)"></div>
</section>
<div class="abs slide-arrow" style="left:8px"><svg width="28" height="32" viewBox="0 0 28 32" aria-hidden="true"><path d="M16 11l-5 5 5 5" fill="none" stroke="#fff" stroke-width="2"/></svg></div>
<div class="abs slide-arrow" style="left:1154px"><svg width="28" height="32" viewBox="0 0 28 32" aria-hidden="true"><path d="M12 11l5 5-5 5" fill="none" stroke="#fff" stroke-width="2"/></svg></div>
<div class="abs tagline"><b>bramble ridge podiatry</b> is a podiatry clinic in the heart of melbourne CBD</div>

<section>
  <h1 class="abs section-title welcome-title">Welcome to Bramble Ridge Podiatry</h1>
  <svg class="abs title-rule" viewBox="0 0 546 14" aria-hidden="true"><circle cx="6" cy="7" r="5" fill="#c9c9c9"/><circle cx="24" cy="7" r="6" fill="#c9c9c9"/><circle cx="42" cy="7" r="5" fill="#c9c9c9"/><line x1="52" y1="7" x2="546" y2="7" stroke="#c9c9c9"/></svg>
  <div class="abs welcome-copy">
    <p>Bramble Ridge Podiatry is a Podiatry clinic in the heart of Melbourne CBD. We are located between Arden &amp; Tallow Streets in the Harbourline Business Centre / Larchmont Hotel Complex.</p>
    <p>Our podiatrists are fully qualified health professionals who are able to diagnose, treat, manage or help to prevent all medical conditions that affect the feet and lower limb.</p>
    <p style="margin-top:28px"><a class="read-more">Read More</a></p>
  </div>
  <div class="abs video" role="img" aria-label="Video of a podiatrist examining a patient's foot">
    <svg width="330" height="222" viewBox="0 0 330 222">
      <defs><linearGradient id="vid" x1="0" y1="0" x2="1" y2="1"><stop offset="0" stop-color="#c9d2dc"/><stop offset="1" stop-color="#e9c7b3"/></linearGradient></defs>
      <rect width="330" height="192" fill="url(#vid)"/>
      <rect x="142" y="78" width="46" height="34" rx="7" fill="#111"/>
      <path d="M159 86l14 9-14 9z" fill="#fff"/>
      <rect y="192" width="330" height="30" fill="#1d1d1f"/>
      <path d="M12 201l9 6-9 6z" fill="#fff"/>
      <path d="M32 204h4l5-4v14l-5-4h-4z" fill="#fff"/>
      <rect x="62" y="205" width="180" height="4" rx="2" fill="#555"/>
      <rect x="62" y="205" width="82" height="4" rx="2" fill="#d21f1f"/>
      <path d="M306 200h6v2h-4v4h-2zM318 214h-6v-2h4v-4h2z" fill="#fff"/>
    </svg>
  </div>
</section>

<section class="abs services">
  <div class="abs notch" style="top:0;border-top-color:#fff;border-bottom:0"></div>
</section>
<h2 class="abs services-title">Our <span>Services</span></h2>
<svg class="abs" style="left:423px;top:894px" width="354" height="14" viewBox="0 0 354 14" aria-hidden="true"><g fill="#9d95b5"><circle cx="5" cy="7" r="4"/><circle cx="17" cy="7" r="4"/><circle cx="31" cy="7" r="6"/><circle cx="323" cy="7" r="6"/><circle cx="337" cy="7" r="4"/><circle cx="349" cy="7" r="4"/></g><line x1="40" y1="7" x2="314" y2="7" stroke="#9d95b5"/></svg>
<p class="abs services-intro">We provide General Podiatry Treatment and some Specialised Services in relation to various foot conditions, including</p>

<div class="abs service" style="left:117px;top:980px">
  <div class="service-icon"><div class="service-art" role="img" aria-label="Illustration of a knee joint"></div></div>
  <h3>Sports Injuries</h3>
  <p>Using Veritas's ClearScan platform, we will scan your website and generate a report outlining areas where....{+}</p>
  <a>Read More</a>
</div>
<div class="abs service-divider" style="left:428px"></div>
<div class="abs service" style="left:441px;top:980px">
  <div class="service-icon"><div class="service-art" role="img" aria-label="Illustration of a person resting in bed at night"></div></div>
  <h3>Orthotic Therapy</h3>
  <p>Veritas uses a combination of manual evaluation and automated testing for its Compliance audits. ...{+}</p>
  <a>Read More</a>
</div>
<div class="abs service-divider" style="left:777px"></div>
<div class="abs service" style="left:780px;top:980px">
  <div class="service-icon"><div class="service-art" role="img" aria-label="Illustration of toes with sore nails"></div></div>
  <h3>Nail Surgery</h3>
  <p>Veritas can assit you with your accessibility determinations &amp; advise on remediation techniques....{+}</p>
  <a>Read More</a>
</div>

<section class="abs news-band" role="img" aria-label="Soft blurred background of a laptop in use">
  <div class="abs notch" style="top:0;border-top-color:var(--deep);border-bottom:0"></div>
</section>

<div class="abs" style="left:131px;top:1430px;width:430px">
  <div style="display:flex;align-items:center;gap:14px">
    <svg width="36" height="30" viewBox="0 0 36 30" aria-hidden="true"><path d="M4 2h20a4 4 0 0 1 4 4v10a4 4 0 0 1-4 4H12l-7 6v-6H4a4 4 0 0 1-4-4V6a4 4 0 0 1 4-4z" fill="#6b449b"/><path d="M30 10h2a4 4 0 0 1 4 4v8a4 4 0 0 1-4 4v4l-6-4h-8a4 4 0 0 1-3-2h9a6 6 0 0 0 6-6z" fill="#9a86c6"/></svg>
    <h2 class="block-title">Latest Blog Posts</h2>
    <svg style="margin-left:auto" width="42" height="20" viewBox="0 0 42 20" aria-hidden="true"><g fill="none" stroke="#999" stroke-width="1.5"><circle cx="10" cy="10" r="8"/><circle cx="32" cy="10" r="8"/><path d="M12 6l-4 4 4 4M30 6l4 4-4 4"/></g></svg>
  </div>
  <div class="block-rule" style="margin-top:10px"></div>
</div>
<article class="abs post" style="top:1508px">
  <div class="post-thumb" role="img" aria-label="Author portrait" style="background:linear-gradient(135deg,#8a7a6a,#5a4a3e)"></div>
  <div><h4>Ut tellus dolor, dapibus smit dollar nomk egemop</h4><time>15.08.2015</time><p>Utm tellus dolor, dapibus eget, elemen velmki cursu eleifelitas. Aenean auctorbni wisi et urnam. Aliquam at volutpatis <span>[...]</span></p></div>
</article>
<article class="abs post" style="top:1634px">
  <div class="post-thumb" role="img" aria-label="Author portrait" style="background:linear-gradient(135deg,#9a6a6a,#5e4444)"></div>
  <div><h4>Ut tellus dolor, dapibus smit dollar nomk egemop</h4><time>15.08.2015</time><p>Utm tellus dolor, dapibus eget, elemen velmki cursu eleifelitas. Aenean auctorbni wisi et urnam. Aliquam at volutpatis <span>[...]</span></p></div>
</article>

<div class="abs" style="left:633px;top:1430px;width:435px">
  <h2 class="block-title">Our Accreditations</h2>
  <div class="block-rule" style="margin-top:10px;background:linear-gradient(90deg,var(--accent) 0 110px,#999 110px)"></div>
</div>
<div class="abs badge" style="left:637px;top:1525px"><i style="background:#e8a23a"></i></div>
<div class="abs badge" style="left:863px;top:1525px"><i style="background:#2b5ea8"></i></div>
<div class="abs badge" style="left:637px;top:1628px"><i style="background:#3b3b3b"></i></div>
<div class="abs badge" style="left:863px;top:1628px"><i style="background:#1c9a48"></i></div>

<section class="abs cta"></section>
<div class="abs cta-button">Book An Appointment</div>
<p class="abs cta-text">We are eligible service providers for all <em>VCA Gold Card holders.</em><br>RoadCare &amp; WorkShield accepted. On the spot health insurance</p>

<footer class="abs site-footer"></footer>
<div class="abs quick-links">
  <h3 class="foot-head">Quick Links</h3>
  <ul><li>Consulting</li><li>Inspections</li><li>Training</li><li>General Contracing</li><li>Clients</li><li>Contact Us</li></ul>
</div>
<div class="abs contact-col">
  <h3 class="foot-head" style="border:0">Contact Details</h3>
  <div class="contact-row"><svg width="12" height="16" viewBox="0 0 12 16" aria-hidden="true"><path d="M6 0a6 6 0 0 1 6 6c0 4-6 10-6 10S0 10 0 6a6 6 0 0 1 6-6z" fill="#333"/><circle cx="6" cy="6" r="2.2" fill="#fff"/></svg><span>Suite 212 / 75 Harlow<br>Street  Melbourne  3000</span></div>
  <div class="contact-row" style="padding:22px 0"><svg width="14" height="14" viewBox="0 0 14 14" aria-hidden="true"><path d="M2 0l3 3-1.5 2c1 2 2.5 3.5 4.5 4.5L10 8l3 3-2 2C6 13 1 8 1 3z" fill="#333"/></svg><span>1300 555 014</span></div>
  <div class="contact-row" style="border:0;padding-top:18px"><svg width="14" height="11" viewBox="0 0 14 11" aria-hidden="true"><rect width="14" height="11" fill="#333"/><path d="M0 0l7 6 7-6" fill="none" stroke="#fff"/></svg><span>info@brambleridgepodiatry.net</span></div>
</div>
<div class="abs hours-col">
  <h3 class="foot-head">Hours of Operation</h3>
  <dl style="margin-top:14px">
    <dt>Monday to Friday</dt><dd>10:00am to 07:00pm</dd>
    <dt>Saturday</dt><dd>10:00am to 05:00pm</dd>
    <dt>Sunday</dt><dd style="border:0">By Appointment Only</dd>
  </dl>
</div>
<div class="abs foot-logo"><i></i><span>Bramble<br>Ridge<br>Podiatry</span></div>

<div class="abs bottom-bar"></div>
<p class="abs copyright">Copyright © 2016 Northvale Studio Services.  All Right Reserved.</p>
<span class="abs social" style="left:973px"></span>
<span class="abs social" style="left:1015px"></span>
<span class="abs social" style="left:1057px"></span>

</body>
</html>
```